Laser Tattoo Removal Business Cards

We are looking for a professional business card design for a laser tattoo removal business. Ideally looking for a black business card design. The name of the business is Brightline Tattoo Removal. We place our cards at local tattoo shops so we ideally are looking for something trendy/edgy to draw both male and female clientele in.

Target Market(s)

Male/Female ages 18-60

Contact Information for Business Card

black background ideally.. hoping to stay within greys, whites and black

Font styles to use
Serif
Sans Serif

Colors
121212
a9a9a9
5c5c5c
f5f5f5
ffffff
7f7f7f
606060
848484
9d9d9d

Requirements
Must have
• Employee Info:
• Melissa Thornbury
• Chief Executive Offer
• m: 919.537.2846
• w: 919.362.4178
• f: 919.685.3907
• mthornbury@brightlinetattooremoval.example
• Address:
• 4615 Oakmere Pkwy, Suite 210
• Raleigh, NC 27654
• Website:
• www.brightlinetattooremoval.example
Nice to have
• Myabe business name on back or logo on back and employee info on the front

```html
<!DOCTYPE html>
<html lang="en">
<head>
<meta charset="utf-8">
<title>Brightline Tattoo Removal – Business Card</title>
<link href="https://fonts.googleapis.com/css2?family=Lato:wght@400;900&family=Arimo:wght@400&display=swap" rel="stylesheet">
<style>
  :root {
    --card-black: #121212;
    --stage: #2e2e2e;
    --white: #ffffff;
    --soft-white: #f5f5f5;
    --rule: #5c5c5c;
    --grey-light: #a9a9a9;
    --grey-mid: #7f7f7f;
  }
  * { box-sizing: border-box; margin: 0; padding: 0; }
  html, body { width: 1200px; height: 896px; overflow: hidden; }
  body {
    background: var(--stage);
    display: flex;
    flex-direction: column;
    align-items: center;
    justify-content: center;
    gap: 24px;
    font-family: "Arimo", Arial, sans-serif;
    color: var(--soft-white);
  }
  .card {
    position: relative;
    width: 720px;
    height: 412px;
    background: var(--card-black);
    box-shadow: 0 6px 18px rgba(0,0,0,.45);
  }
  .brand {
    position: absolute;
    text-align: center;
    font-family: "Lato", sans-serif;
    font-weight: 400;
    color: var(--white);
    text-transform: uppercase;
    letter-spacing: 5px;
    line-height: 1.35;
  }
  .brand-name { font-size: 40px; display: block; letter-spacing: 6px; }
  .brand-sub { font-size: 15px; display: block; letter-spacing: 6px; }
  .rule {
    position: absolute;
    height: 1px;
    background: var(--rule);
  }

  /* front */
  .front .brand { left: 360px; top: 108px; width: 330px; }
  .front .rule { left: 300px; right: 34px; top: 250px; }
  .person { position: absolute; left: 44px; top: 112px; }
  .person-name {
    font-family: "Lato", sans-serif;
    font-weight: 900;
    font-size: 21px;
    text-transform: uppercase;
    color: var(--white);
  }
  .person-title { font-size: 17px; color: var(--soft-white); margin-top: 2px; }
  .phones { list-style: none; margin-top: 12px; }
  .phones li {
    display: flex; align-items: center; gap: 10px;
    font-size: 18px; line-height: 26px; color: var(--white);
  }
  .phones svg { width: 14px; height: 14px; fill: var(--grey-light); }
  .address {
    position: absolute; right: 38px; top: 276px;
    text-align: right; font-size: 19px; line-height: 27px; color: var(--white);
  }

  /* back */
  .back .brand { left: 0; right: 0; top: 104px; }
  .back .rule { left: 150px; right: 150px; top: 230px; }
  .web {
    position: absolute; left: 0; right: 0; top: 256px;
    text-align: center; font-size: 19px; line-height: 28px; color: var(--soft-white);
  }
</style>
</head>
<body>

<section class="card front" aria-label="Card front">
  <div class="person">
    <p class="person-name">Melissa Thornbury</p>
    <p class="person-title">Chief Executive Officer</p>
    <ul class="phones">
      <li><svg viewBox="0 0 14 14" aria-label="mobile"><path d="M3 0h8v14H3zM4.5 1.5v9h5v-9z"/></svg>919.537.2846</li>
      <li><svg viewBox="0 0 14 14" aria-label="work phone"><path d="M3 1l2 0 1 3-1.5 1.2a8 8 0 0 0 4.3 4.3L10 8l3 1v2c0 1-1 2-2 2A11 11 0 0 1 1 3c0-1 1-2 2-2z"/></svg>919.362.4178</li>
      <li><svg viewBox="0 0 14 14" aria-label="fax"><path d="M3 1h6l2 2v3H3zM1 6h12v6h-2v-2H3v2H1zM4 11h6v2H4z"/></svg>919.685.3907</li>
    </ul>
  </div>

  <div class="brand">
    <span class="brand-name">Brightline</span>
    <span class="brand-sub">Tattoo Removal</span>
  </div>
  <div class="rule"></div>

  <address class="address" style="font-style:normal">
    4615 Oakmere Pkwy, Suite 210<br>
    Raleigh, NC 27654
  </address>
</section>

<section class="card back" aria-label="Card back">
  <div class="brand">
    <span class="brand-name">Brightline</span>
    <span class="brand-sub">Tattoo Removal</span>
  </div>
  <div class="rule"></div>
  <p class="web">
    mthornbury@brightlinetattooremoval.example<br>
    www.brightlinetattooremoval.example
  </p>
</section>

</body>
</html>
```